Business Card Design Project

We are not a new company, but renamed to "Vantorin Kitchens" last year. We specialize in modern high-end cabinetry imports. We would like to communicate a sense of quality and cutting edge technology. Ideally the design would incorporate our logo colors, silver, red and preferably a black, matte background. Though we are open to suggestions.
Logo is attached.
Edit: I have attached rough drafts of the previous cards, this way you will have all necessary content that needs to go on the cards.
Updates
Project Deadline Extended
Reason: We have received a lot of great designs, but due to the sheer number we couldn't respond to all. We will extend the deadline for another 7 days to finalize and provide feedback to designers.
Thank you for your hard work!
Industry/Entity Type
Business
Look and feel
Each slider illustrates characteristics of the customer's brand and the style your logo design should communicate.

```html
<!DOCTYPE html>
<html lang="en">
<head>
<meta charset="utf-8">
<title>Vantorin Kitchens – Business Cards</title>
<link rel="stylesheet" href="https://fonts.googleapis.com/css2?family=Arimo:wght@400;700&display=swap">
<style>
  :root {
    --bg: #e6e6ea;
    --card-black: #050505;
    --silver: #c9c9cc;
    --silver-light: #e4e4e6;
    --silver-text: #b8b8bc;
    --red: #d0161c;
    --ink: #151515;
    --white: #ffffff;
  }
  * { margin: 0; padding: 0; box-sizing: border-box; }
  html, body {
    width: 1200px; height: 987px; overflow: hidden;
    background: var(--bg);
    font-family: "Arimo", Arial, sans-serif;
  }
  .stage { position: relative; width: 1200px; height: 987px; }
  .card {
    position: absolute;
    width: 520px; height: 300px;
    border-radius: 30px;
    overflow: hidden;
    background: var(--card-black);
    box-shadow: 0 18px 40px rgba(0,0,0,0.25);
  }
  .card--front { left: 50px; top: 344px; }
  .card--back { left: 630px; top: 344px; }
  .card__bg { position: absolute; inset: 0; }

  .brand {
    position: absolute; left: 0; right: 0;
    display: flex; align-items: center; justify-content: center; gap: 10px;
    color: var(--silver-text);
    font-weight: 700;
    letter-spacing: 2px;
    text-transform: uppercase;
  }
  .brand__mark { width: 16px; height: 16px; background: var(--silver-text); }
  .card--front .brand { top: 48px; font-size: 26px; }
  .card--back .brand { top: 128px; font-size: 32px; }
  .card--back .brand__mark { width: 20px; height: 20px; }

  .holder {
    position: absolute; left: 160px; top: 104px;
    color: var(--white); font-size: 17px;
  }
  .holder__name { font-weight: 700; letter-spacing: 0.5px; }
  .holder__role { font-weight: 400; }

  .contact {
    position: absolute; left: 30px; top: 170px;
    color: var(--ink); font-size: 14.5px; line-height: 25px;
    list-style: none;
  }
  .contact__line { display: flex; align-items: center; gap: 6px; white-space: nowrap; }
  .icon { width: 13px; height: 13px; flex: none; }
  .gap { width: 8px; }
</style>
</head>
<body>
<main class="stage">

  <section class="card card--front" aria-label="Card front">
    <svg class="card__bg" viewBox="0 0 520 300" width="520" height="300" aria-hidden="true">
      <defs>
        <linearGradient id="silverFill" x1="0" y1="0" x2="1" y2="1">
          <stop offset="0" stop-color="#d6d6d9"/>
          <stop offset="1" stop-color="#b5b5b9"/>
        </linearGradient>
      </defs>
      <path d="M0 140 C 360 140, 500 162, 520 272 L520 300 L0 300 Z" fill="url(#silverFill)"/>
      <path d="M0 136 C 362 136, 504 158, 524 272" fill="none" stroke="#d0161c" stroke-width="3"/>
    </svg>

    <div class="brand"><span class="brand__mark"></span>Vantorin Kitchens</div>

    <p class="holder"><span class="holder__name">MARCUS DELAINE</span>, <span class="holder__role">Director</span></p>

    <ul class="contact">
      <li class="contact__line">
        <svg class="icon" viewBox="0 0 16 16" aria-label="Phone"><circle cx="8" cy="8" r="7" fill="none" stroke="#151515" stroke-width="1.5"/><path d="M5 5 Q5 11 11 11" fill="none" stroke="#151515" stroke-width="2"/></svg>
        780.555.0142
        <span class="gap"></span>
        <svg class="icon" viewBox="0 0 16 16" aria-label="Fax"><rect x="2" y="6" width="12" height="8" rx="1" fill="#151515"/><rect x="5" y="2" width="6" height="5" fill="#151515"/></svg>
        780.555.0187
      </li>
      <li class="contact__line">
        <svg class="icon" viewBox="0 0 16 16" aria-label="Mobile"><rect x="4" y="1" width="8" height="14" rx="1.5" fill="#151515"/><rect x="5.5" y="3" width="5" height="6" fill="#c9c9cc"/></svg>
        780.555.0163
        <span class="gap"></span>
        <svg class="icon" viewBox="0 0 16 16" aria-label="Email"><rect x="1" y="3" width="14" height="10" rx="1" fill="#151515"/><path d="M1.5 4 L8 9 L14.5 4" fill="none" stroke="#c9c9cc" stroke-width="1.2"/></svg>
        marcus@vantorinkitchens.ca
      </li>
      <li class="contact__line">4120 - 87 St., Edmonton, AB T6E 2K4</li>
    </ul>
  </section>

  <section class="card card--back" aria-label="Card back">
    <div class="brand"><span class="brand__mark"></span>Vantorin Kitchens</div>
  </section>

</main>
</body>
</html>
```